Yoga/movement guide/teacher for adult yoga practice and kid yoga

What is the positioning or mission statement of your company? to guide individuals in a yoga-based safe and sustainable movement practice applicable to all ages and body types. Currently my focus is working with children in daycare and school settings, but my goal is to expand into private yoga practice for adults, and potentially as part of rented space in studios. I hope to find a way to work with children AND adults (so would love for logo to be appealing to both), but current focus is with children based on need and demand in the community. yoga for children also compliments my backround as a pediatrician/neonatologist, and I greatly miss interacting with children. I also want to emphasize a yoga/movement practice that is focused more on what one feels internally through movement. NOT what one looks like asthetically. I believe in removing all mirrors from yoga/movement practice. It should be an experience of movement/poses/yoga through appropriate cueing and education. It is not about the details of how far the knee should bend, or how high the leg should be. Focusing on foudation first, core, then core engagement and ultimately expression of poses/movements. A focus on strength, stability and mobility, not just flexibility, which is the common perception/association with yoga. I also want individuals to learn to be an advocate of their own health. Through guidance, I hope for individuals to connect with their body so they know themselves so well to be able to advocate for themselves in the modern healthcare world. This internal experience and connection is so essential in a world where modern medicine has become a business and it is all about making a dollar. the connection with patients is lost, and individuals need to learn to empower themselves and through their new found voice to be able to articulate what is wrong.<br/>Does your company have a tagline or slogan that should be included with the logo? "Move From Within"<br/>What do you hope your company can be known for? Accessible yoga for a sustained practice. A guided movement practice where one gains information and knowledge of oneself through a mind/body connection. For one feel good physically with a new awaraness of their internal radiance that exists in all beings. Physical rejuvenation egnites a light and increases energy to flow through the physical body, which ultimately tranlates into works of kindness for others and out in the world. <br/>What color palettes might you prefer? why? love the colors currently chosen<br/>Where will the logo be primarily used? initially business cards, but hopefully future websites, t-shirts, and potentially local magazine adds. Also starting with a small couple of banners for community events in the area. I currently practice as a nomad out of my car :)<br/>Are there any elements you would prefer to see in the logo? Movement. A modern depiction of a human body/figure practicing movement. Hoping to avoid a stereotypical yoga pose per say, just because I want to people to think of it more of a movement practice with yoga roots. Modern yoga. There are elements of breathing and connecting with oneself through the flow of breath and movement, but I do not focus on the meditative/cerebral aspect of the yoga practice. What I teach is almost reaching a meditative state through movement. I personally don't practice, nor resonate with just seated meditation. just not my thing :)<br/>In your opinion, what defines a well-designed logo? curiosity. enough info for individuals to think they know what it means, but want to know more. invokes curiosity, but not too abstract. Reproducible. not too complicated. I want also to invoke a community feel, so a design that appeals to all people within a community. <br/>What is your preference in reference to icons, typography, spokespeople (characters), etc.? modern design. I love the idea of a logo for my purposes, to invoke a sense of movement from within. So not too static. <br/>What words or icons must be included in the logo? movement with yoga roots. <br/>What logos do you like and why? A representation, but not exact. I think some ambiguity is intriguing for others, and also memorable. I want it to be an artistic representation of movement/yoga<br/>What logos do you dislike and why? too busy, too loud. <br/>In your opinion, what is the primary purpose for a logo? association<br/>Who is the primary target audience? (who is most likely to use your services/product?) Children and their parents, but ultimately to expand into teaching adults. I even have aspirations of prenatal and post-natal yoga. Potentially incorporating infants. <br/>Who currently uses your product the most? n/a (working in schools/daycare currently. It is currently all volunteer)<br/>Are you pleased with the range of people your company serves? n/a<br/>Are you looking to expand, modify, or completely change your target audience? or will it remain the same? yes! expand into an adult audience. <br/>How do you plan to focus on your target audience? currently by working through schools and daycares. hopefully ultimately through after school care programs and then offering kid yoga in an existing yoga studio (working on this with Q Studio in Ridgeland, currently)<br/>What are your main forms of advertising? word of mouth, schools, daycares. Happy kids talking to their parents about the yoga class they took and happy teachers :)<br/>How do most customers find out about your company?<br/>Which gender are you targeting? All genders! However, with kid yoga, often the maternal individual in the child's life is more involved with decision making as far as extracurricular activities

Target Market(s)

individuals and families interested in wellness and feeling great

Contact Information for Business Card

Dana Whitford
Yoga Instructor
RYT-200, RCYT

certified yoga teacher for adults and children

Colors

Designer to choose colors to be used in the design.

Requirements
Must have
• "Move From Within"
Nice to have
• logo with same colors

```html
<!DOCTYPE html>
<html lang="en">
<head>
<meta charset="utf-8">
<title>Brightfold Studios — Business Card</title>
<link href="https://fonts.googleapis.com/css2?family=Roboto:wght@300;400;700&display=swap" rel="stylesheet">
<style>
  :root {
    --stage: #3b3b3d;
    --paper: #ffffff;
    --teal: #62c6cf;
    --teal-deep: #4fb7c1;
    --sun: #f5d93e;
    --ink-light: #ffffff;
  }
  * { margin: 0; padding: 0; box-sizing: border-box; }
  html, body {
    width: 1200px; height: 901px; overflow: hidden;
    background: var(--stage);
    font-family: "Roboto", Arial, sans-serif;
  }
  .canvas { position: relative; width: 1200px; height: 901px; }
  .card {
    position: absolute; left: 250px; width: 700px; height: 400px;
    overflow: hidden; box-shadow: 0 6px 18px rgba(0,0,0,.35);
  }
  .card--back { top: 30px; background: var(--paper); }
  .card--front { top: 471px; background: var(--teal); }

  /* back side: centered wordmark */
  .brand {
    position: absolute; left: 50%; top: 50%; transform: translate(-50%, -50%);
    display: flex; flex-direction: column; align-items: center;
    white-space: nowrap;
  }
  .brand__name {
    display: flex; align-items: center; gap: 14px;
    font-weight: 300; font-size: 48px; line-height: 1; color: var(--teal-deep); letter-spacing: 1px;
  }
  .brand__dot { width: 34px; height: 34px; border-radius: 50%; background: var(--sun); flex: none; }
  .brand__tagline {
    margin-top: 14px; padding-left: 48px; font-weight: 400; font-size: 11px; letter-spacing: 4px;
    text-transform: uppercase; color: var(--teal-deep);
  }

  /* front side */
  .front-field { position: absolute; inset: 0; }
  .mini-brand {
    position: absolute; right: 34px; top: 30px;
    display: flex; align-items: center; gap: 8px; white-space: nowrap;
    font-weight: 300; font-size: 20px; line-height: 1; color: var(--ink-light);
  }
  .mini-brand__dot { width: 16px; height: 16px; border-radius: 50%; background: var(--sun); flex: none; }
  .contact {
    position: absolute; left: 395px; top: 150px; color: var(--ink-light); white-space: nowrap;
  }
  .contact__name {
    font-weight: 700; font-size: 25px; color: var(--sun); text-transform: uppercase;
    letter-spacing: .5px; line-height: 1.2;
  }
  .contact__role { font-weight: 300; font-size: 17px; margin-top: 2px; }
  .contact__cred { font-weight: 300; font-size: 14px; margin-top: 2px; }
  .contact__address { font-weight: 300; font-size: 16px; line-height: 1.3; margin-top: 18px; }
  .contact__list { list-style: none; margin-top: 14px; font-weight: 300; font-size: 16px; }
  .contact__list li { display: flex; align-items: center; gap: 10px; line-height: 1.5; }
  .contact__icon { width: 16px; height: 16px; flex: none; }
</style>
</head>
<body>
<main class="canvas">

  <section class="card card--back" aria-label="Card back">
    <div class="brand">
      <div class="brand__name"><span class="brand__dot"></span>Brightfold Studios</div>
      <p class="brand__tagline">Move From Within</p>
    </div>
  </section>

  <section class="card card--front" aria-label="Card front">
    <svg class="front-field" width="700" height="400" viewBox="0 0 700 400" aria-hidden="true">
      <path d="M0 120 C140 140 250 250 320 400 L0 400 Z" fill="var(--sun)"/>
    </svg>

    <div class="mini-brand"><span class="mini-brand__dot"></span>Brightfold Studios</div>

    <div class="contact">
      <h1 class="contact__name">Dana Whitford</h1>
      <p class="contact__role">Yoga Instructor</p>
      <p class="contact__cred">RYT-200, RCYT</p>
      <p class="contact__address">Your address, city<br>state, ZIP 0000</p>
      <ul class="contact__list">
        <li>
          <svg class="contact__icon" viewBox="0 0 16 16"><path d="M3.5 1.5l2.5 3-1.5 1.8c.8 1.8 2.3 3.3 4.2 4.2L10.5 9l3 2.5-1.2 2.6C6.5 14 2 9.5 1.9 3.7z" fill="var(--sun)"/></svg>
          555-014-2100
        </li>
        <li>
          <svg class="contact__icon" viewBox="0 0 16 16"><rect x="1" y="3" width="14" height="10" fill="var(--sun)"/><path d="M1 3l7 6 7-6" fill="none" stroke="var(--teal)" stroke-width="1.3"/></svg>
          hello@brightfoldyoga.com
        </li>
        <li>
          <svg class="contact__icon" viewBox="0 0 16 16"><circle cx="8" cy="8" r="7" fill="var(--sun)"/><path d="M1 8h14M8 1c-3 3-3 11 0 14M8 1c3 3 3 11 0 14" fill="none" stroke="var(--teal)" stroke-width="1.1"/></svg>
          www.brightfoldyoga.com
        </li>
      </ul>
    </div>
  </section>

</main>
</body>
</html>
```